International oil and gas consultancy business needs a web design

Hello, I need a web design for a new oil and gas auditing consultancy business. My business undertakes contract audit assignments to review past costs of oil and gas operations (see attached Excel file for more details of the businesses services). I need the design to give the impression of a professional consultancy style of business, rather than a retail style of website. Note: this job is for LAYOUT DESIGN ONLY and not coding / development work.
The following are my key design principles:
1. BASIC DESIGN: I am after a simple and static web design. I don't want the pages busy or cluttered with too many images or detail.
2. HORIZONTAL TABS: I require a horizontal set of tabs towards the top of the screens (see Excel file) which remain in the same position on every page.
3. META TAG PLANNING: The design should allow for effective positioning of content so that key meta tag words can easily be built during the technical build stage.
4. NUMBER OF PAGES: The site will eventually have a maximum of 10 pages. Seven of the pages will reside under the tabs. Can you please present your opening submission for the first two page.
5. USE OF MY LOGO: The attached logo (JPEG file) should be used throughout the website. Please don't change the shape and colour.
6. COLOUR SCHEMES: Can you please consider any of the 3 colour schemes below:
A - dark red (to match the logo), light grey and perhaps another of your liking;
B - dark red (to match the logo), light cream and perhaps another of your liking;
C - dark red (to match the logo), white and perhaps another of your liking.
7. WORD CONTENT: I have attached an Excel file which shows the estimated word content for each page.
8. FUTURE USE OF DESIGN: I'm planning on building a Wordpress website. Can you please ensure the layout design supports this application.

Target Market(s)

oil and gas companies (small and large)

Industry/Entity Type

Oil And Gas

Font styles to use
Sans Serif

Requirements
Nice to have
• The KRL logo and business name should ideally be next to each other. Also, the logo and name should be part of the background graphics, not above it.

```html
<!DOCTYPE html>
<html lang="en">
<head>
<meta charset="utf-8">
<title>KRL – Kestrel Resource Ledgers</title>
<link href="https://fonts.googleapis.com/css2?family=Questrial&family=Open+Sans:wght@400;600&display=swap" rel="stylesheet">
<style>
:root{
  --red:#b8212a;
  --red-dark:#8e1a20;
  --red-light:#d42a31;
  --nav-top:#c8262e;
  --nav-bottom:#a11b23;
  --text:#555;
  --muted:#6a6a6a;
  --line:#dcdcdc;
  --icon:#a9a9a9;
  --arrow-bg:#2f3136;
}
*{box-sizing:border-box;margin:0;padding:0}
html,body{width:1200px;height:1055px;overflow:hidden;background:#fff}
body{position:relative;font-family:"Open Sans",sans-serif;color:var(--text)}
.brand{position:absolute;left:126px;top:8px;color:var(--red);font-family:"Questrial",sans-serif;font-weight:400}
.brand-mark{font-size:72px;line-height:74px;letter-spacing:2px}
.brand-name{font-size:14.5px;letter-spacing:.2px;margin-top:6px;padding-left:11px;white-space:nowrap}
.social{position:absolute;right:124px;top:74px;display:flex;gap:8px}
.social span{width:24px;height:24px;border-radius:50%;background:var(--icon)}
.main-nav{position:absolute;left:116px;top:114px;width:968px;height:49px;border-radius:4px;
  background:linear-gradient(var(--nav-top),var(--nav-bottom));overflow:hidden}
.main-nav a{position:absolute;top:0;height:49px;color:#fff;text-decoration:none;font-family:"Questrial",sans-serif;font-size:16px;
  line-height:49px;text-transform:uppercase;white-space:nowrap}
.main-nav a.active{left:0;width:113px;text-align:center;background:var(--red-light)}
.main-nav a:nth-child(2){left:134px}
.main-nav a:nth-child(3){left:256px}
.main-nav a:nth-child(4){left:372px}
.main-nav a:nth-child(5){left:533px}
.main-nav a:nth-child(6){left:663px}
.main-nav a:nth-child(7){left:835px}
.hero{position:absolute;left:116px;top:169px;width:968px;height:389px;border-radius:4px;
  background:linear-gradient(180deg,#a9c7e6 0%,#dbe6ef 40%,#c9c9c6 70%,#9b9d9c 100%)}
.hero-arrow{position:absolute;top:148px;width:30px;height:66px;background:var(--arrow-bg);display:flex;align-items:center;justify-content:center}
.hero-arrow.prev{left:0;border-radius:0 3px 3px 0}
.hero-arrow.next{right:3px;border-radius:3px 0 0 3px}
.intro{position:absolute;left:117px;top:592px;width:630px}
.intro h1{font-family:"Questrial",sans-serif;font-weight:400;color:var(--red-dark);font-size:23px;line-height:30px;white-space:nowrap}
.intro p{font-size:13.2px;line-height:22.7px;margin-top:6px;color:var(--muted)}
.services{position:absolute;left:116px;top:715px;display:flex;gap:9px}
.service{position:relative;width:200px;height:108px;background:linear-gradient(160deg,#8a8f96,#4b4f56)}
.service:nth-child(2){background:linear-gradient(160deg,#b6c2cc,#6f6a6a)}
.service:nth-child(3){background:linear-gradient(160deg,#6f6761,#40403f)}
.service-label{position:absolute;left:0;right:0;bottom:0;height:32px;background:rgba(160,30,38,.82);
  color:#fff;font-family:"Questrial",sans-serif;font-size:15.5px;line-height:32px;padding-left:14px;white-space:nowrap}
.service-label svg{position:absolute;right:10px;top:8px}
.summary{position:absolute;left:116px;top:847px;width:630px;font-size:12.6px;line-height:21px;color:var(--muted)}
.news{position:absolute;left:789px;top:593px;width:293px;height:323px;border:1px solid var(--line);border-radius:3px;
  background:linear-gradient(#fff 80%,#f1f1f1);padding:22px 27px}
.news h2{font-family:"Questrial",sans-serif;font-weight:400;font-size:23px;color:#222;margin-bottom:14px;white-space:nowrap}
.news-item{margin-bottom:17px}
.news-item h3{font-weight:400;font-size:12.6px;color:var(--red);line-height:18px;white-space:nowrap}
.news-item p{font-size:10.8px;line-height:19px;color:var(--muted)}
.site-footer{position:absolute;left:0;top:985px;width:1200px;border-top:1px solid var(--line);height:70px;font-size:12.6px;color:#333}
.copyright{position:absolute;left:118px;top:23px;white-space:nowrap}
.legal{position:absolute;right:110px;top:23px;color:#777;white-space:nowrap}
.legal span{margin:0 7px;color:#999}
</style>
</head>
<body>
<header>
  <div class="brand">
    <div class="brand-mark">KRL</div>
    <div class="brand-name">KESTREL RESOURCE LEDGERS</div>
  </div>
  <div class="social" aria-label="Social links"><span></span><span></span><span></span></div>
  <nav class="main-nav">
    <a class="active" href="#">Home</a>
    <a href="#">About Us</a>
    <a href="#">Services</a>
    <a href="#">Our Partners</a>
    <a href="#">Approach</a>
    <a href="#">Why Choose Us</a>
    <a href="#">Contact Us</a>
  </nav>
</header>
<section class="hero" role="img" aria-label="Photo of an oil and gas processing plant with tall silver tanks and pipework under a blue sky">
  <span class="hero-arrow prev"><svg width="12" height="26" viewBox="0 0 12 26"><path d="M10 1 2 13l8 12" fill="none" stroke="#fff" stroke-width="1.5"/></svg></span>
  <span class="hero-arrow next"><svg width="12" height="26" viewBox="0 0 12 26"><path d="M2 1l8 12-8 12" fill="none" stroke="#fff" stroke-width="1.5"/></svg></span>
</section>
<main>
  <div class="intro">
    <h1>Kestrel Resource Ledgers is a Perth (Australia)</h1>
    <p>based firm specialising in providing quality audit services for the oil and gas industry. Our skills and knowledge of oil and gas, along with a deep understanding of business commercial needs, ensures the high quality of our services.</p>
  </div>
  <div class="services">
    <div class="service" role="img" aria-label="Photo of an engineer in a hard hat at a plant">
      <div class="service-label">Joint Venture Audits<svg width="10" height="18" viewBox="0 0 10 18"><path d="M1 1l8 8-8 8" fill="none" stroke="#fff" stroke-width="1.5"/></svg></div>
    </div>
    <div class="service" role="img" aria-label="Photo of a site worker in a hard hat">
      <div class="service-label">Contract Audits<svg width="10" height="18" viewBox="0 0 10 18"><path d="M1 1l8 8-8 8" fill="none" stroke="#fff" stroke-width="1.5"/></svg></div>
    </div>
    <div class="service" role="img" aria-label="Photo of two managers in hard hats reviewing a site">
      <div class="service-label">Operations Audits<svg width="10" height="18" viewBox="0 0 10 18"><path d="M1 1l8 8-8 8" fill="none" stroke="#fff" stroke-width="1.5"/></svg></div>
    </div>
  </div>
  <p class="summary">Mauris vel lacus vitae felis vestibulum volutpat Etiam est nunc venenatis in tristique eu imperdiet ac nisl Cum sociis natoque penatibus et magnis dis parturient montes nascetur ridiculus mus In iaculis facilisis massa Etiam eu urna Sed porta Suspendisse quam leo molestie sed luctus quis feugiat in pede</p>
  <aside class="news">
    <h2>News &amp; Projects</h2>
    <div class="news-item"><h3>Vivamus porttitor purus</h3><p>Curabitur vel mi sit amet magna malesuada ultrices Ut nisi erat fermentum vel congue id euismod in elit Fusce ultricies orci</p></div>
    <div class="news-item"><h3>Mauris vel lacus vitae felis</h3><p>Curabitur vel mi sit amet magna malesuada ultrices Ut nisi erat fermentum vel</p></div>
    <div class="news-item"><h3>Phasellus felis dolor scelerisque</h3><p>Curabitur vel mi sit amet magna malesuada ultrices Ut nisi erat fermentum vel</p></div>
  </aside>
</main>
<footer class="site-footer">
  <div class="copyright">Copyright © 2014 Kestrel Resource Ledgers</div>
  <div class="legal">Term and Conditions<span>|</span>Privacy Policy</div>
</footer>
</body>
</html>
```